Vision, Mission and Culture Posters

We have written text paragraphs for our company vision and mission and need them made into a2 or a3 sized posters using our logo for inspiration for colour. Our company culture has 10 paragraphs and we'd like this to be a single poster of a2 or a1. Each poster should have the logo on and share common design. It's not a complex job really.

Industry/Entity Type

It Company

Requirements
Nice to have
• These will be going up on our office wall so need to be clear to read from a distance and look professional but also not stodgy.

```html
<!DOCTYPE html>
<html lang="en">
<head>
<meta charset="utf-8">
<title>Kerbside Bay Hire — Mission</title>
<link rel="stylesheet" href="https://fonts.googleapis.com/css2?family=Anton&family=Archivo+Black&family=Montserrat:wght@700;800;900&family=Roboto+Condensed:wght@700&display=swap">
<style>
  :root {
    --brand-yellow: #fff200;
    --brand-red: #d7282f;
    --ink: #111111;
    --paper: #f6f6f4;
    --paper-edge: #f0ecb4;
    --body-grey: #4a4a4a;
    --white: #ffffff;
  }
  * { margin: 0; padding: 0; box-sizing: border-box; }
  html, body { width: 1200px; height: 849px; overflow: hidden; }
  body { background: var(--paper); }

  .poster {
    position: relative;
    width: 1200px;
    height: 849px;
    overflow: hidden;
    background: radial-gradient(ellipse 62% 60% at 50% 52%, var(--paper) 55%, var(--paper-edge) 100%);
    font-family: "Montserrat", Arial, sans-serif;
  }

  .poster__bands { position: absolute; inset: 0; width: 1200px; height: 849px; }

  .brand-plate {
    position: absolute;
    left: 105px; top: 29px;
    width: 368px; height: 108px;
    background: var(--brand-yellow);
    border: 4px solid var(--ink);
    border-radius: 12px;
    display: flex;
    align-items: center;
    justify-content: center;
    gap: 16px;
  }
  .brand-plate__mark {
    width: 26px; height: 26px;
    background: var(--brand-red);
  }
  .brand-plate__name {
    font-family: "Montserrat", Arial, sans-serif;
    font-weight: 800;
    font-size: 29px;
    line-height: 1.1;
    color: var(--ink);
    text-align: center;
  }

  .title-plate {
    position: absolute;
    left: 539px; top: 28px;
    width: 388px; height: 110px;
    background: var(--ink);
    border-radius: 12px;
    display: flex;
    align-items: center;
    justify-content: center;
  }
  .title-plate__text {
    font-family: "Anton", Impact, sans-serif;
    font-size: 112px;
    line-height: 1;
    color: var(--brand-yellow);
    letter-spacing: 1px;
    transform: translateY(3px);
  }

  .mission {
    position: absolute;
    left: 0; top: 180px;
    width: 1200px;
    text-align: center;
  }
  .mission__lead {
    font-family: "Archivo Black", Arial Black, sans-serif;
    font-size: 50px;
    line-height: 58px;
    color: var(--ink);
    letter-spacing: 1px;
  }
  .mission__goal {
    font-family: "Anton", Impact, sans-serif;
    font-size: 64px;
    line-height: 66px;
    color: var(--brand-red);
    letter-spacing: 0.4px;
    margin-top: -2px;
  }
  .mission__scope {
    font-family: "Montserrat", Arial, sans-serif;
    font-weight: 800;
    font-size: 26px;
    line-height: 34px;
    color: var(--ink);
    letter-spacing: -0.6px;
    margin-top: 2px;
  }

  .belief {
    position: absolute;
    left: 36px; top: 368px;
    width: 1129px; height: 193px;
    background: var(--ink);
    border-radius: 16px;
    padding: 5px;
  }
  .belief__frame {
    width: 100%; height: 100%;
    border: 3px solid var(--white);
    border-radius: 12px;
    display: flex;
    align-items: center;
    justify-content: center;
  }
  .belief__text {
    font-family: "Montserrat", Arial, sans-serif;
    font-weight: 900;
    font-size: 33px;
    line-height: 43px;
    color: var(--white);
    text-transform: uppercase;
    text-align: center;
    letter-spacing: -1px;
  }
  .belief__highlight { color: var(--brand-yellow); }

  .approach {
    position: absolute;
    left: 60px; top: 592px;
    width: 1080px;
    font-family: "Roboto Condensed", Arial Narrow, sans-serif;
    font-weight: 700;
    font-size: 38px;
    line-height: 46px;
    color: var(--body-grey);
    text-align: center;
  }
</style>
</head>
<body>
<main class="poster">
  <svg class="poster__bands" viewBox="0 0 1200 849" aria-hidden="true">
    <path d="M0 0 H1200 V64 C1150 100 1110 150 1060 163 C1050 166 1045 167 1035 167 L0 153 Z" fill="var(--brand-yellow)"/>
    <path d="M0 153 L1035 167 C1045 167 1050 166 1060 163 C1110 150 1150 100 1200 64" fill="none" stroke="var(--ink)" stroke-width="2"/>
    <path d="M0 826 L1150 810 C1175 809 1190 812 1200 818 V849 H0 Z" fill="var(--brand-red)" stroke="var(--ink)" stroke-width="2"/>
  </svg>

  <div class="brand-plate">
    <span class="brand-plate__mark"></span>
    <span class="brand-plate__name">Kerbside<br>Bay Hire</span>
  </div>

  <div class="title-plate">
    <h1 class="title-plate__text">MISSION</h1>
  </div>

  <section class="mission">
    <p class="mission__lead">Our mission is to</p>
    <p class="mission__goal">ACHIEVE GREAT CUSTOMER SATISFACTION</p>
    <p class="mission__scope">in everything we do and offer for meeting our customers parking needs.</p>
  </section>

  <section class="belief">
    <div class="belief__frame">
      <p class="belief__text">We believe our path to achieving this comes through<br>giving a <span class="belief__highlight">simple yet thorough and friendly service</span> to<br>our customers without unnecessary complication.</p>
    </div>
  </section>

  <p class="approach">We will achieve this through using the technology available to us, continual staff training and development, regular refinement of our practices and processes along with commitment to our roles and the foundations for building our success.</p>
</main>
</body>
</html>
```